Woman owned consulting company needs an elegant and modern business card design

I need a business card design for my new consulting company, Mara Quillon Consulting. I am looking for something that is simple and elegant, but also creative and original. You can use either version of the logo that are attached. I have also included the information that needs to be featured on the business card.

Contact Information for Business Card

Requirements
Must have
• The logo and the font type and a standard business card size. Use shades of gray/silver and or rose gold that are in the logo.
• I didn't realize that my actual logo wasn't attached. Please incorporate in the designs.
Should not have
• Colors that are different from my logo

```html
<!DOCTYPE html>
<html lang="en">
<head>
<meta charset="utf-8">
<title>Mara Quillon Consulting — Business Card</title>
<link href="https://fonts.googleapis.com/css2?family=Arimo:wght@400;700&display=swap" rel="stylesheet">
<style>
  :root {
    --backdrop: #3e3e3e;
    --card-stock: #828282;
    --foil: #e8e8e8;
    --foil-soft: #d6d6d6;
  }
  * { margin: 0; padding: 0; box-sizing: border-box; }
  html, body {
    width: 1200px;
    height: 1016px;
    overflow: hidden;
    background: var(--backdrop);
  }
  body {
    position: relative;
    font-family: "Arimo", Arial, sans-serif;
    color: var(--foil);
  }
  .card {
    position: absolute;
    left: 332px;
    width: 549px;
    height: 314px;
    background: var(--card-stock);
  }
  .card--front { top: 131px; }
  .card--back  { top: 514px; }

  .card__title {
    position: absolute;
    left: 61px;
    top: 56px;
    font-size: 16px;
    letter-spacing: 0.2px;
    white-space: nowrap;
  }
  .card__name { font-weight: 700; }
  .card__divider { font-weight: 400; margin: 0 8px; color: var(--foil-soft); }
  .card__role { font-weight: 400; color: var(--foil-soft); }

  .card__contact {
    position: absolute;
    left: 61px;
    top: 207px;
    list-style: none;
    font-size: 11px;
    line-height: 19px;
    color: var(--foil-soft);
    letter-spacing: 0.1px;
  }

  .card__monogram {
    position: absolute;
    right: 60px;
    top: 204px;
    font-size: 50px;
    font-weight: 400;
    letter-spacing: -1px;
    line-height: 1;
  }

  .card__brand {
    position: absolute;
    left: 0;
    right: 0;
    top: 112px;
    text-align: center;
    font-weight: 400;
    color: var(--foil);
  }
  .card__brand-name {
    display: block;
    font-size: 46px;
    line-height: 1;
    letter-spacing: 1px;
  }
  .card__brand-tag {
    display: block;
    margin-top: 10px;
    font-size: 13px;
    letter-spacing: 20px;
    padding-left: 20px;
  }
</style>
</head>
<body>
  <section class="card card--front" aria-label="Business card front">
    <p class="card__title">
      <span class="card__name">MARA QUILLON</span><span class="card__divider">/</span><span class="card__role">OWNER</span>
    </p>
    <ul class="card__contact">
      <li>610-555-0142</li>
      <li>MARA@MARAQUILLONCONSULTING.COM</li>
      <li>WWW.MARAQUILLONCONSULTING.COM</li>
    </ul>
    <p class="card__monogram">MQC</p>
  </section>

  <section class="card card--back" aria-label="Business card back">
    <p class="card__brand">
      <span class="card__brand-name">Mara Quillon</span>
      <span class="card__brand-tag">CONSULTING</span>
    </p>
  </section>
</body>
</html>
```